BildeVOLD buisnesscard

Hey :) I need a modern buisnesscard for my company BildeVOLD
It most have:
Dagligleder og Fotograf: Henrik Audun Strandvik

Mob: +4791264085
Epost: post@bildevold.example
Adresse: Kvernbakken9, 6040 Fjordvik

Facbook and instagram logo with text BildeVOLD

BildeVOLD logo

It Company

```html
<!DOCTYPE html>
<html lang="no">
<head>
<meta charset="utf-8">
<title>BildeVOLD – visittkort</title>
<link href="https://fonts.googleapis.com/css2?family=Noto+Sans:wght@400;700&display=swap" rel="stylesheet">
<style>
  :root {
    --backdrop: #e6e6e6;
    --card: #262626;
    --ink: #a8a8a8;
    --ink-strong: #a3a3a3;
    --glyph: #262626;
    --frame: #bdbdbd;
  }
  * { box-sizing: border-box; margin: 0; padding: 0; }
  html, body { width: 1200px; height: 1200px; overflow: hidden; }
  body {
    background: var(--backdrop);
    font-family: "Noto Sans", Verdana, sans-serif;
    color: var(--ink);
    position: relative;
  }
  .card {
    position: absolute;
    left: 240px;
    width: 720px;
    height: 434px;
    background: var(--card);
    box-shadow: 0 6px 14px rgba(0,0,0,0.25);
  }
  .card--front { top: 106px; }
  .card--back { top: 624px; }

  .corner { position: absolute; width: 42px; height: 42px; border-color: var(--frame); border-style: solid; border-width: 0; }
  .corner--tl { left: 24px; top: 24px; border-left-width: 1.5px; border-top-width: 1.5px; }
  .corner--tr { right: 24px; top: 24px; border-right-width: 1.5px; border-top-width: 1.5px; }
  .corner--bl { left: 24px; bottom: 24px; border-left-width: 1.5px; border-bottom-width: 1.5px; }
  .corner--br { right: 24px; bottom: 24px; border-right-width: 1.5px; border-bottom-width: 1.5px; }

  .person { position: absolute; right: 374px; top: 97px; text-align: right; }
  .person__name { font-size: 26px; line-height: 30px; letter-spacing: 0.3px; white-space: nowrap; }
  .person__role { font-size: 16px; line-height: 20px; margin-top: 3px; letter-spacing: 0.4px; white-space: nowrap; }

  .contact { position: absolute; left: 0; width: 360px; list-style: none; }
  .contact__item {
    position: absolute; right: 0; display: flex; align-items: center; gap: 10px;
    font-size: 19px; line-height: 24px; letter-spacing: 0.4px; text-align: right;
  }
  .contact__text { width: 300px; white-space: nowrap; }
  .contact__icon { width: 28px; height: 28px; flex: none; }
  .contact__icon circle { fill: var(--ink-strong); }
  .contact__icon .glyph { fill: var(--glyph); stroke: none; }
  .contact__icon .glyph-line { fill: none; stroke: var(--glyph); stroke-width: 1.6; }

  .brand { position: absolute; font-weight: 700; color: var(--ink-strong); white-space: nowrap; }
  .brand--front { left: 528px; top: 250px; transform: translate(-50%, -50%); font-size: 48px; letter-spacing: 0.5px; }
  .brand--back { left: 360px; top: 220px; transform: translate(-50%, -50%); font-size: 84px; letter-spacing: 1px; }

  .social { position: absolute; top: 332px; left: 0; width: 100%; display: flex; justify-content: center; gap: 28px; }
  .social__item { display: flex; align-items: center; gap: 10px; font-size: 19px; letter-spacing: 0.4px; }
  .social__mark { width: 34px; height: 34px; border: 2px solid var(--ink-strong); border-radius: 50%; }
</style>
</head>
<body>

<section class="card card--front" aria-label="Visittkort forside">
  <span class="corner corner--tl"></span><span class="corner corner--tr"></span>
  <span class="corner corner--bl"></span><span class="corner corner--br"></span>

  <div class="person">
    <p class="person__name">Henrik Audun Strandvik</p>
    <p class="person__role">Dagligleder og Fotograf</p>
  </div>

  <ul class="contact">
    <li class="contact__item" style="top:175px;">
      <span class="contact__text">Kvernbakken9<br>6040 Fjordvik</span>
      <svg class="contact__icon" viewBox="0 0 28 28" aria-hidden="true">
        <circle cx="14" cy="14" r="14"/>
        <path class="glyph" d="M14 6.5a5 5 0 0 0-5 5c0 3.8 5 10 5 10s5-6.2 5-10a5 5 0 0 0-5-5zm0 7a2 2 0 1 1 0-4 2 2 0 0 1 0 4z"/>
      </svg>
    </li>
    <li class="contact__item" style="top:235px;">
      <span class="contact__text">+47 912 64 085</span>
      <svg class="contact__icon" viewBox="0 0 28 28" aria-hidden="true">
        <circle cx="14" cy="14" r="14"/>
        <path class="glyph" d="M9.5 7l3 0.5 1 3.5-2 1.5a10 10 0 0 0 4.5 4.5l1.5-2 3.5 1 0.5 3-1.5 1.5C14 21 7 14 8 8.5z"/>
      </svg>
    </li>
    <li class="contact__item" style="top:272px;">
      <span class="contact__text">www.bildevold.example</span>
      <svg class="contact__icon" viewBox="0 0 28 28" aria-hidden="true">
        <circle cx="14" cy="14" r="14"/>
        <circle class="glyph-line" cx="14" cy="14" r="7.5" style="fill:none"/>
        <path class="glyph-line" d="M6.5 14h15M14 6.5c-3 3-3 12 0 15M14 6.5c3 3 3 12 0 15"/>
      </svg>
    </li>
    <li class="contact__item" style="top:309px;">
      <span class="contact__text">post@bildevold.example</span>
      <svg class="contact__icon" viewBox="0 0 28 28" aria-hidden="true">
        <circle cx="14" cy="14" r="14"/>
        <rect class="glyph" x="7.5" y="9.5" width="13" height="9" rx="1"/>
        <path d="M8 10l6 4.5 6-4.5" fill="none" stroke="#a3a3a3" stroke-width="1.4"/>
      </svg>
    </li>
  </ul>

  <p class="brand brand--front">BildeVOLD</p>
</section>

<section class="card card--back" aria-label="Visittkort bakside">
  <span class="corner corner--tl"></span><span class="corner corner--tr"></span>
  <span class="corner corner--bl"></span><span class="corner corner--br"></span>

  <p class="brand brand--back">BildeVOLD</p>

  <div class="social">
    <span class="social__item"><span class="social__mark"></span>BildeVOLD</span>
    <span class="social__item"><span class="social__mark"></span>BildeVOLD</span>
  </div>
</section>

</body>
</html>
```